Bry7Legal Letterhead

Need a new letterhead for my law firm.
IDENTIFYING INFORMATION BELOW:
Anselmo R Quintara III
Attorney at Law
Address: 2847 Larkspur Blvd, Ste 300, Dallas, TX 75204
Phone: 877-482-6017
Fax: 469-738-1452
Email: bry@bry7legal.example
Website: www.bry7legal.example

Colors
0054AA
0677BA
7BADD7
CADEEF
E8F1F8

Requirements
Must have
• Logo needs to be on the letterhead, along with identifying information which is included in the project description.

```html
<!DOCTYPE html>
<html lang="en">
<head>
<meta charset="utf-8">
<title>Bry7Legal Letterhead</title>
<link href="https://fonts.googleapis.com/css2?family=Montserrat:wght@400;500;600;700&family=Kaushan+Script&display=swap" rel="stylesheet">
<style>
  :root {
    --ink: #1b1b1b;
    --text: #3a3a3a;
    --muted: #6b6b6b;
    --brand-blue: #0677BA;
    --brand-deep: #0054AA;
    --brand-light: #7BADD7;
    --brand-pale: #CADEEF;
    --paper: #ffffff;
    --backdrop: #E8F1F8;
    --rule: #2a2a2a;
  }
  * { box-sizing: border-box; margin: 0; padding: 0; }
  html, body { width: 1200px; height: 900px; overflow: hidden; }
  body {
    background: var(--backdrop);
    font-family: "Montserrat", Arial, sans-serif;
    color: var(--text);
    position: relative;
  }
  .letterhead {
    position: absolute;
    left: 290px; top: 12px;
    width: 620px; height: 876px;
    background: var(--paper);
    box-shadow: 0 6px 24px rgba(0, 40, 90, 0.15);
    overflow: hidden;
  }
  .firm-name {
    position: absolute; left: 56px; top: 62px;
    font-weight: 700; font-size: 24px;
    color: var(--ink);
  }
  .contact {
    position: absolute; top: 42px; right: 40px;
    display: flex; gap: 14px;
    font-size: 9.5px; line-height: 1.55; color: var(--text); font-weight: 500;
  }
  .contact-group {
    border-left: 1.5px solid var(--rule);
    padding-left: 10px;
    display: flex; flex-direction: column; gap: 2px;
  }
  .contact-row { display: flex; align-items: flex-start; gap: 6px; }
  .contact-row svg { width: 10px; height: 10px; margin-top: 2px; flex: none; fill: var(--brand-blue); }
  .letter { position: absolute; left: 56px; top: 190px; width: 510px; }
  .date { font-size: 11px; color: var(--muted); font-weight: 500; }
  .sender-name { margin-top: 30px; font-size: 13.5px; font-weight: 700; color: var(--ink); }
  .sender-title { font-size: 11.5px; color: var(--muted); margin-top: 2px; }
  .salutation { margin-top: 36px; font-size: 11.5px; color: var(--muted); font-weight: 500; }
  .body-copy p { margin-top: 18px; font-size: 8.6px; line-height: 1.9; color: var(--text); font-weight: 500; }
  .closing { margin-top: 48px; font-size: 11px; color: var(--muted); font-weight: 500; }
  .signature { font-family: "Kaushan Script", cursive; font-size: 24px; color: var(--ink); margin-top: 2px; }
  .footer-accent {
    position: absolute; left: 0; right: 0; bottom: 40px;
    height: 6px; background: var(--brand-light);
  }
  .footer-band {
    position: absolute; left: 0; right: 0; bottom: 0;
    height: 40px; background: var(--brand-deep);
    display: flex; align-items: center; justify-content: flex-end;
    padding-right: 40px;
  }
  .footer-url { font-size: 9px; font-weight: 600; color: var(--paper); }
</style>
</head>
<body>
  <main class="letterhead">
    <div class="firm-name">Bry7Legal</div>

    <div class="contact">
      <div class="contact-group">
        <div class="contact-row">
          <svg viewBox="0 0 10 10" aria-hidden="true"><path d="M2 0.5 L3.8 2.8 L2.8 3.8 Q4 6.2 6.2 7.2 L7.2 6.2 L9.5 8 L8.3 9.5 Q3.5 9.5 0.5 1.7 Z"/></svg>
          <span>877-482-6017</span>
        </div>
        <div class="contact-row">
          <svg viewBox="0 0 10 10" aria-hidden="true"><rect x="2.5" y="0.5" width="5" height="3"/><rect x="0.5" y="4" width="9" height="5" rx="1"/></svg>
          <span>469-738-1452</span>
        </div>
      </div>
      <div class="contact-group">
        <div class="contact-row">
          <svg viewBox="0 0 10 10" aria-hidden="true"><path d="M0.5 2 H9.5 V8.5 H0.5 Z M1 2.5 L5 5.5 L9 2.5" stroke="#fff" stroke-width="0.8"/></svg>
          <span>bry@bry7legal.example</span>
        </div>
        <div class="contact-row">
          <svg viewBox="0 0 10 10" aria-hidden="true"><path d="M5 0.5 A3.5 3.5 0 0 1 8.5 4 C8.5 6.5 5 9.5 5 9.5 C5 9.5 1.5 6.5 1.5 4 A3.5 3.5 0 0 1 5 0.5 Z M5 2.6 A1.4 1.4 0 1 0 5 5.4 A1.4 1.4 0 1 0 5 2.6 Z"/></svg>
          <span>2847 Larkspur Blvd,<br>Ste 300, Dallas,<br>TX 75204</span>
        </div>
      </div>
    </div>

    <section class="letter">
      <div class="date">01 March, 2022</div>
      <div class="sender-name">Anselmo R Quintara III</div>
      <div class="sender-title">Attorney at Law</div>
      <div class="salutation">Dear Sir,</div>
      <div class="body-copy">
        <p>Anselmo R. Quintara, III, Attorney at Law, PLLC is a Texas personal injury law firm representing individuals who have been injured in accidents. We understand the ramifications an injury of any size can have on your life and are dedicated to assisting every one of our clients in obtaining the care and restitution they deserve.</p>
        <p>By concentrating his practice exclusively on protecting the rights of personal injury victims, Bry can use the experience and knowledge he’s gained to enable him to provide his clients unparalleled representation. Every case that Bry handles receives his personal attention, and all initial consultations are provided free of charge. If Bry can’t get you a settlement, his representation will cost you $0.00.</p>
        <p>Bry appreciates the stress and inconvenience a personal injury causes and understands the importance of being able to contact your attorney directly with your questions and concerns. Because of this, his client’s have direct access to him 24 hours a day, 7 days a week, 365 days a year.</p>
        <p>If you have suffered a personal injury contact Anselmo R. Quintara III, Attorney at Law, PLLC for a free evaluation of your case. I’m available at your convenience – contact me online, or call 877-482-6017 for assistance 24/7/365.</p>
      </div>
      <div class="closing">Sencerly Yours</div>
      <div class="signature">Your Name</div>
    </section>

    <div class="footer-accent"></div>
    <footer class="footer-band">
      <span class="footer-url">www.bry7legal.example</span>
    </footer>
  </main>
</body>
</html>
```